Lorvex Tilo medical cannibis cultivation company

tag - Tilo rise
Lorvex Tilo medical cannabis cultivation - logo is selected- can we please see bold examples with our selection. We are mainly dealing with medical companies and professionals. We would like to be stand out in the crowd with our designs. Welcome any and all attempts. Thanks

Target Market(s)

Medical and Professional

Industry/Entity Type

Medical And Science

Font styles to use
Sans Serif

Colors

Designer to choose colors to be used in the design.

Requirements
Must have
• Bright colour and be bold- Love the teal and magenta that is currently on the dark background design.
Nice to have
• shading and the 3D affect- The shadowed appearance.
Should not have
• Anything related to illegal activity or un professional manners

```html
<!DOCTYPE html>
<html lang="en">
<head>
<meta charset="utf-8">
<title>Lorvex Tilo — Business Card</title>
<link href="https://fonts.googleapis.com/css2?family=Marcellus&display=swap" rel="stylesheet">
<style>
  :root {
    --stage: #2b2b2d;
    --teal: #00adef;
    --magenta: #9c4e9a;
    --white: #ffffff;
    --grey: #9a9fa4;
    --card-radius: 26px;
  }
  * { margin: 0; padding: 0; box-sizing: border-box; }
  html, body {
    width: 1125px; height: 1200px; overflow: hidden;
    background: var(--stage);
    font-family: "Marcellus", serif;
  }
  .card {
    position: absolute;
    left: 150px;
    width: 825px; height: 471px;
    border-radius: var(--card-radius);
    overflow: hidden;
  }
  .card-front { top: 98px; background: var(--teal); color: var(--white); }
  .card-back { top: 630px; background: var(--white); }

  .split-band { position: absolute; inset: 0; }

  .brand { position: absolute; left: 50px; top: 38px; width: 330px; }
  .brand-name {
    font-size: 46px; line-height: 1; letter-spacing: 0.5px;
    white-space: nowrap;
  }
  .tagline {
    display: flex; align-items: center; gap: 10px;
    font-size: 20px; letter-spacing: 2px; margin-top: 6px;
    white-space: nowrap;
  }
  .tagline::before, .tagline::after {
    content: ""; flex: 1; height: 2px; background: currentColor;
  }

  .person { position: absolute; left: 50px; top: 158px; }
  .person-name { font-size: 34px; letter-spacing: 1px; line-height: 1.1; }
  .person-role { font-size: 23px; letter-spacing: 0.5px; line-height: 1.2; }

  .address { position: absolute; left: 50px; top: 236px; font-size: 19px; line-height: 25px; }

  .contacts { position: absolute; left: 50px; top: 298px; list-style: none; font-size: 19px; }
  .contacts li { display: flex; align-items: center; height: 26.3px; }
  .contacts svg { width: 18px; height: 18px; margin-right: 12px; fill: var(--white); }

  .back-mark {
    position: absolute; left: 327px; top: 99px;
    width: 172px; height: 172px;
    border: 5px solid var(--grey); border-radius: 50%;
  }
  .back-brand {
    position: absolute; left: 0; right: 0; top: 280px;
    display: flex; flex-direction: column; align-items: center;
  }
  .back-brand .brand-name { font-size: 50px; color: var(--teal); }
  .back-brand .tagline { color: var(--grey); width: 292px; font-size: 21px; margin-top: 4px; }
</style>
</head>
<body>

<section class="card card-front">
  <svg class="split-band" viewBox="0 0 825 471" preserveAspectRatio="none" aria-hidden="true">
    <polygon points="572,0 825,0 825,471 506,471" fill="var(--magenta)"/>
  </svg>

  <div class="brand">
    <div class="brand-name">LORVEX TILO</div>
    <div class="tagline">TILO RISE</div>
  </div>

  <div class="person">
    <div class="person-name">OWEN MARSH</div>
    <div class="person-role">CEO/FOUNDER</div>
  </div>

  <address class="address" style="font-style: normal;">
    4120 Alder Court<br>
    Juneau, Alaska 31286
  </address>

  <ul class="contacts">
    <li>
      <svg viewBox="0 0 24 24"><path d="M6.6 10.8a15.1 15.1 0 0 0 6.6 6.6l2.2-2.2c.3-.3.7-.4 1-.2 1.1.4 2.3.6 3.6.6.6 0 1 .4 1 1V20c0 .6-.4 1-1 1A17 17 0 0 1 3 4c0-.6.4-1 1-1h3.5c.6 0 1 .4 1 1 0 1.3.2 2.5.6 3.6.1.3 0 .7-.2 1z"/></svg>
      615 204 7731
    </li>
    <li>
      <svg viewBox="0 0 24 24"><path d="M7 1h10a2 2 0 0 1 2 2v18a2 2 0 0 1-2 2H7a2 2 0 0 1-2-2V3a2 2 0 0 1 2-2zm0 3v14h10V4zm5 15.5a1.2 1.2 0 1 0 0 2.4 1.2 1.2 0 0 0 0-2.4z"/></svg>
      842 519 3068
    </li>
    <li>
      <svg viewBox="0 0 24 24"><path d="M6 2h10v6H6zM2 9h20v9H2zm3 3v2h14v-2zM4 19h16v3H4z"/></svg>
      473 926 5182
    </li>
    <li>
      <svg viewBox="0 0 24 24"><path d="M2 5h20v14H2zm2 2v.5l8 5.5 8-5.5V7l-8 5.3z"/></svg>
      owen@lorvextilo.com
    </li>
    <li>
      <svg viewBox="0 0 24 24"><path d="M12 2a10 10 0 1 0 0 20 10 10 0 0 0 0-20zm-1 17.9A8 8 0 0 1 4.2 10L9 15v1a2 2 0 0 0 2 2zm6.9-2.5A2 2 0 0 0 16 16h-1v-3a1 1 0 0 0-1-1H8v-2h2a1 1 0 0 0 1-1V7h2a2 2 0 0 0 2-2v-.4a8 8 0 0 1 2.9 12.8z"/></svg>
      www.lorvextilo.com
    </li>
  </ul>
</section>

<section class="card card-back">
  <div class="back-mark" aria-hidden="true"></div>
  <div class="back-brand">
    <div class="brand-name">LORVEX TILO</div>
    <div class="tagline">TILO RISE</div>
  </div>
</section>

</body>
</html>
```